Custom Seed Packet design for Flower Farm

We need a design for our seeds packets.
The design will be a kind of "fill in the blanks" as we need the design to be adaptable for multiple varieties of seed. We will be using the design for a rubber stamp.
Our seed packets are 90x90mm in size.
Black logo only. No colour required.
A vintage botanical influence is desired.
Will need to include the following info,
"Wrenfield Gable Co logo" , "Seeds", "Plant Type", "Variety", "Harvested"

```html
<!DOCTYPE html>
<html lang="en">
<head>
<meta charset="utf-8">
<title>Flower Seeds Packet Stamp</title>
<link href="https://fonts.googleapis.com/css2?family=Cormorant+Garamond:wght@500;600&family=Kaushan+Script&display=swap" rel="stylesheet">
<style>
  :root {
    --kraft: #d9c6a2;
    --ink: #1f1b17;
    --ornament-tone: #b9a27c;
    --art-tone: #bfa781;
  }
  html, body {
    margin: 0;
    padding: 0;
    width: 1122px;
    height: 1200px;
    overflow: hidden;
    background: var(--kraft);
  }
  .canvas {
    position: relative;
    width: 1122px;
    height: 1200px;
  }
  .stamp-frame {
    position: absolute;
    left: 81px;
    top: 120px;
    width: 960px;
    height: 960px;
    box-sizing: border-box;
    border: 3px solid var(--ink);
  }
  .ornament {
    position: absolute;
    background: var(--ornament-tone);
  }
  .ornament--h { width: 240px; height: 56px; }
  .ornament--v { width: 56px; height: 180px; }
  .tl.ornament--h { left: 10px; top: 10px; }
  .tl.ornament--v { left: 10px; top: 72px; }
  .tr.ornament--h { right: 10px; top: 10px; }
  .tr.ornament--v { right: 10px; top: 72px; }
  .bl.ornament--h { left: 10px; bottom: 10px; }
  .bl.ornament--v { left: 10px; bottom: 72px; height: 140px; }
  .br.ornament--h { right: 10px; bottom: 10px; }
  .br.ornament--v { right: 10px; bottom: 72px; height: 140px; }

  .seeds-kicker {
    position: absolute;
    left: 0;
    width: 100%;
    top: 68px;
    text-align: center;
    font-family: "Kaushan Script", cursive;
    font-size: 36px;
    color: var(--ink);
    line-height: 1;
  }
  .seeds-title {
    position: absolute;
    left: 0;
    width: 100%;
    top: 112px;
    text-align: center;
    font-family: "Cormorant Garamond", serif;
    font-weight: 500;
    font-size: 92px;
    letter-spacing: 0.32em;
    text-indent: 0.32em;
    color: var(--ink);
    line-height: 1;
  }
  .botanical-art {
    position: absolute;
    left: 50%;
    top: 270px;
    width: 240px;
    height: 210px;
    transform: translateX(-50%);
    border-radius: 50% 50% 42% 42%;
    background: radial-gradient(circle at 50% 45%, var(--art-tone) 0%, var(--art-tone) 45%, var(--kraft) 100%);
  }
  .farm-name {
    position: absolute;
    left: 0;
    width: 100%;
    top: 522px;
    text-align: center;
    font-family: "Cormorant Garamond", serif;
    font-weight: 600;
    font-size: 52px;
    color: var(--ink);
    line-height: 1;
  }
  .field {
    position: absolute;
    left: 101px;
    right: 99px;
    display: flex;
    align-items: flex-end;
    gap: 14px;
  }
  .field-label {
    font-family: "Kaushan Script", cursive;
    font-size: 26px;
    color: var(--ink);
    line-height: 1;
    white-space: nowrap;
  }
  .field-line {
    flex: 1;
    border-bottom: 2px solid var(--ink);
    margin-bottom: 2px;
  }
  .field--type { top: 694px; }
  .field--variety { top: 760px; }
  .field--harvested { top: 824px; }
</style>
</head>
<body>
  <div class="canvas">
    <div class="stamp-frame">
      <div class="ornament ornament--h tl" role="img" aria-label="Vintage filigree corner ornament"></div>
      <div class="ornament ornament--v tl" role="img" aria-label="Vintage filigree corner ornament"></div>
      <div class="ornament ornament--h tr" role="img" aria-label="Vintage filigree corner ornament"></div>
      <div class="ornament ornament--v tr" role="img" aria-label="Vintage filigree corner ornament"></div>
      <div class="ornament ornament--h bl" role="img" aria-label="Vintage filigree corner ornament"></div>
      <div class="ornament ornament--v bl" role="img" aria-label="Vintage filigree corner ornament"></div>
      <div class="ornament ornament--h br" role="img" aria-label="Vintage filigree corner ornament"></div>
      <div class="ornament ornament--v br" role="img" aria-label="Vintage filigree corner ornament"></div>

      <div class="seeds-kicker">Flower</div>
      <div class="seeds-title">SEEDS</div>

      <div class="botanical-art" role="img" aria-label="Line drawing of three poppy blooms on slender stems"></div>
      <div class="farm-name">Wrenfield Gable Co</div>

      <div class="field field--type"><span class="field-label">Plant Type</span><span class="field-line"></span></div>
      <div class="field field--variety"><span class="field-label">Variety</span><span class="field-line"></span></div>
      <div class="field field--harvested"><span class="field-label">Harvested</span><span class="field-line"></span></div>
    </div>
  </div>
</body>
</html>
```